KLV Plant Services

We are a heavy diesel mechanical business with additional air con certificates, remapping engine rebuilt

Contact Information for Business Card

Company Name, Director Name, Managing Director, Contact details, email and website

Font styles to use
Serif
Script

```html
<!DOCTYPE html>
<html lang="en">
<head>
<meta charset="utf-8">
<title>KLV Plant Services – Business Card</title>
<link rel="stylesheet" href="https://fonts.googleapis.com/css2?family=Poppins:wght@400;500;800&display=swap">
<style>
  :root {
    --navy: #0d0d85;
    --navy-deep: #0a0a6e;
    --ink: #1c1c1c;
    --paper: #ffffff;
    --stage: #e4e4e4;
  }
  * { margin: 0; padding: 0; box-sizing: border-box; }
  html, body { width: 1200px; height: 900px; overflow: hidden; }
  body {
    background: var(--stage);
    font-family: "Poppins", sans-serif;
    position: relative;
  }
  .card {
    position: absolute;
    left: 290px;
    width: 620px;
    height: 354px;
    box-shadow: 0 6px 18px rgba(0,0,0,0.18);
    overflow: hidden;
  }
  .card--back { top: 50px; background: var(--navy); }
  .card--front { top: 470px; background: var(--paper); }

  .back-pattern {
    position: absolute; inset: 0;
    background: linear-gradient(135deg, var(--navy) 0%, var(--navy-deep) 100%);
  }
  .back-brand {
    position: absolute;
    right: 40px; top: 70px;
    color: var(--paper);
    font-weight: 800;
    font-size: 13px;
    line-height: 1;
  }

  .person { position: absolute; left: 60px; top: 150px; }
  .person__name {
    color: var(--navy);
    font-weight: 800;
    font-size: 26px;
    letter-spacing: 0.5px;
    line-height: 1;
  }
  .person__role {
    color: var(--ink);
    font-size: 15px;
    margin-top: 4px;
  }
  .person__rule {
    width: 70px; height: 2px;
    background: var(--navy);
    margin-top: 10px;
  }
  .contact { position: absolute; left: 60px; top: 242px; color: var(--ink); font-size: 15px; line-height: 1.25; }
  .contact__address { margin-bottom: 8px; }
  .contact__row { display: flex; align-items: center; gap: 7px; }
  .contact__row svg { width: 13px; height: 13px; flex: none; }
  .contact__site-name { color: var(--navy); }

  .brand {
    position: absolute;
    right: 50px; top: 88px;
    display: flex; align-items: center; gap: 12px;
    color: var(--navy);
    font-weight: 800;
    font-size: 27px;
    line-height: 1;
  }
  .brand__dot { width: 18px; height: 18px; border-radius: 50%; background: var(--navy); }
</style>
</head>
<body>
  <section class="card card--back">
    <div class="back-pattern" role="img" aria-label="Repeating tone-on-tone company mark pattern across the navy card back"></div>
    <div class="back-brand">KLV Plant Services</div>
  </section>

  <section class="card card--front">
    <div class="brand">
      <span class="brand__dot"></span>
      <span class="brand__name">KLV Plant Services</span>
    </div>

    <div class="person">
      <h1 class="person__name">MARK ELLISON</h1>
      <p class="person__role">Director</p>
      <div class="person__rule"></div>
    </div>

    <div class="contact">
      <p class="contact__address">1250 Harlow Rd Oakridge<br>Falls, GA 30190</p>
      <p class="contact__row">
        <svg viewBox="0 0 16 16" aria-hidden="true"><path d="M4 1l3 3-2 2c1 2 3 4 5 5l2-2 3 3-2 3C7 15 1 9 1 3z" fill="var(--navy)"/></svg>
        555-214-0387
      </p>
      <p class="contact__row">
        <svg viewBox="0 0 16 16" aria-hidden="true"><rect x="1.5" y="3.5" width="13" height="9" fill="none" stroke="var(--navy)" stroke-width="1.5"/><path d="M1.5 3.5L8 9l6.5-5.5" fill="none" stroke="var(--navy)" stroke-width="1.5"/></svg>
        info@klvplantservices.com
      </p>
      <p class="contact__row">
        <svg viewBox="0 0 16 16" aria-hidden="true"><circle cx="8" cy="8" r="6.5" fill="none" stroke="var(--navy)" stroke-width="1.5"/><ellipse cx="8" cy="8" rx="3" ry="6.5" fill="none" stroke="var(--navy)" stroke-width="1.2"/><path d="M1.5 8h13" stroke="var(--navy)" stroke-width="1.2"/></svg>
        <span>www.<span class="contact__site-name">klvplantservices</span>.com</span>
      </p>
    </div>
  </section>
</body>
</html>
```